"Vine Hollow Excursions" is a top notch Santa Barbara County Wine Tour company.

We provide scenic, boutique and custom wine tours. I need the card to be clean and classy. I will provide our logo. I would like the logo to cover the back side of the card as an option and would like to see a couple color options other then our signature green and gold. I would like to see some creative options and let the designers come up with options.
I need cards for myself and my team. The final design should communicate "An authentic and boutique wine tour experience"
Please use my website for reference www.vinehollowexcursions.example

Target Market(s)

We have a wide range of clients from millennials to baby boomers

Industry/Entity Type

Tour

Contact Information for Business Card

Contact info:
Dale Morton
805-219-6384
info@vinehollowexcursions.example
vinehollowexcursions.example

Colors

Designer to choose colors to be used in the design.

Requirements
Must have
• my logo
Nice to have
• *I would like to have the backside side with the logo and the company statement
• "An authentic and boutique wine tour experience" as an option.
• *I would also like to see what the designers can create!
• *I would like to see an option that incorporates or social: instagram, yelp, trip advisor
Should not have
• I do not want it too busy.

```html
<!DOCTYPE html>
<html lang="en">
<head>
<meta charset="utf-8">
<title>Vine Hollow Excursions – Business Card</title>
<link rel="stylesheet" href="https://fonts.googleapis.com/css2?family=Cinzel:wght@500&family=Jost:wght@400&family=Source+Sans+3:wght@400&display=swap">
<style>
  :root {
    --page: #e4e2dc;
    --card-top: #ecebe6;
    --card-top-shade: #dcdbd4;
    --brand-ink: #6f6146;
    --mark: #2b4a36;
    --band-green: #1f4a35;
    --band-green-dark: #173a29;
    --gold: #cdbd8e;
    --gold-soft: #c2b186;
    --icon-a: #8a4a3c;
    --icon-b: #4f7a3c;
    --icon-c: #a3302a;
  }
  * { box-sizing: border-box; margin: 0; padding: 0; }
  html, body {
    width: 1200px;
    height: 969px;
    overflow: hidden;
    background: var(--page);
  }
  .canvas {
    position: relative;
    width: 1200px;
    height: 969px;
  }
  .business-card {
    position: absolute;
    left: 100px;
    top: 200px;
    width: 1000px;
    height: 570px;
    overflow: hidden;
    box-shadow: 0 18px 40px rgba(0,0,0,0.18);
  }
  .card-header {
    position: absolute;
    left: 0;
    top: 0;
    width: 1000px;
    height: 302px;
    background: linear-gradient(180deg, var(--card-top) 0%, var(--card-top-shade) 100%);
  }
  .header-decoration {
    position: absolute;
    left: 0;
    top: 0;
    width: 1000px;
    height: 302px;
  }
  .brand-mark {
    position: absolute;
    left: 440px;
    top: 32px;
    width: 120px;
    height: 120px;
    border-radius: 50%;
    background: var(--mark);
  }
  .brand-name,
  .brand-region {
    position: absolute;
    left: 0;
    width: 1000px;
    text-align: center;
    color: var(--brand-ink);
    font-family: "Cinzel", serif;
    font-weight: 500;
    line-height: 1;
    white-space: nowrap;
  }
  .brand-name {
    top: 176px;
    font-size: 40px;
    letter-spacing: 2px;
  }
  .brand-region {
    top: 244px;
    font-size: 16px;
    letter-spacing: 6px;
  }
  .card-band {
    position: absolute;
    left: 0;
    top: 302px;
    width: 1000px;
    height: 268px;
    background: linear-gradient(180deg, var(--band-green) 0%, var(--band-green-dark) 100%);
    color: var(--gold);
  }
  .band-line {
    position: absolute;
    left: 0;
    width: 1000px;
    text-align: center;
    line-height: 1;
    white-space: nowrap;
  }
  .person-name {
    top: 36px;
    font-family: "Cinzel", serif;
    font-weight: 500;
    font-size: 38px;
    letter-spacing: 1px;
  }
  .tagline {
    top: 89px;
    font-family: "Source Sans 3", sans-serif;
    font-size: 21px;
    color: var(--gold-soft);
  }
  .contact-line {
    top: 124px;
    font-family: "Jost", sans-serif;
    font-size: 25px;
  }
  .website {
    top: 157px;
    font-family: "Jost", sans-serif;
    font-size: 22px;
    color: var(--gold-soft);
  }
  .social-row {
    position: absolute;
    left: 0;
    top: 199px;
    width: 1000px;
    display: flex;
    justify-content: center;
    gap: 16px;
  }
  .social-badge {
    width: 36px;
    height: 36px;
    border-radius: 5px;
  }
  .social-badge--photo { background: var(--icon-a); }
  .social-badge--travel { background: var(--icon-b); }
  .social-badge--reviews { background: var(--icon-c); }
</style>
</head>
<body>
<main class="canvas">
  <section class="business-card">
    <header class="card-header">
      <svg class="header-decoration" viewBox="0 0 1000 302" role="img" aria-label="Faint decoration of vineyard hills and sun rays">
        <defs>
          <radialGradient id="hillGlow" cx="50%" cy="70%" r="70%">
            <stop offset="0%" stop-color="#d6d5cd" stop-opacity="0.9"/>
            <stop offset="100%" stop-color="#e8e7e1" stop-opacity="0"/>
          </radialGradient>
        </defs>
        <rect width="1000" height="302" fill="url(#hillGlow)"/>
      </svg>
      <span class="brand-mark"></span>
      <div class="brand-name">Vine Hollow Excursions</div>
      <div class="brand-region">SANTA BARBARA COUNTY</div>
    </header>
    <div class="card-band">
      <h1 class="band-line person-name">DALE MORTON</h1>
      <p class="band-line tagline">An authentic &amp; boutique wine tour experience</p>
      <p class="band-line contact-line">P. 805-219-6384 E. info@vinehollowexcursions.example</p>
      <p class="band-line website">www.vinehollowexcursions.example</p>
      <div class="social-row">
        <span class="social-badge social-badge--photo"></span>
        <span class="social-badge social-badge--travel"></span>
        <span class="social-badge social-badge--reviews"></span>
      </div>
    </div>
  </section>
</main>
</body>
</html>
```